6 page (for now) squarespace website design for a Mobile Fitness small business

My sons California based small business "BrenVale Coaching" with new subsidiary called "BrenVale 4 Kids". I don't understand coding the website, is that the function squarespace provides?
In the end I want a working website, squarespace, I have a google workspace domain, email and subscription to squarespace & google workspace. URLs include brenvalecoaching.example and brenvale4kids.example. I have an idea of what I am looking for in a website and I have some examples of website designs I like, but I am 100% open to your design concepts and artistic flair. email is torin@brenvalecoaching.example
I am looking for someone to design the site, help me understand how to make "minor" changes and hopefully have a long term relationship on the tech side of the business. I need an Idea of pricing for future changes (Rate T&M).
There are 2 businesses so I need a way to incorporate both the main company and a subsidiary into 1 website or link it somehow. I am open to your suggestions how to accomplish that. Do I need 2 completely separate websites or can it be done on 1 site directing you to different pages. I read conflicting info if it is a BAD idea to link 2 different websites so I will defer to your advice.
Below are the pages I need designed:
- Home Page- BrenVale Coaching
- Home Page- BrenVale 4 Kids (Homeschool market)
- Member Page (subscription service?)
- Workouts- with video clips 1-6 min each
- About
- Contact
- FAQ's
Future work & page designs:
- Store with training subscriptions & a few merch items
- Booking Appointments
- Bookshelf
- email campaign
-Blog
I like the feel of this website:
https://zestlope.example/

```html
<!DOCTYPE html>
<html lang="en">
<head>
<meta charset="utf-8">
<title>BrenVale Coaching</title>
<link rel="stylesheet" href="https://fonts.googleapis.com/css2?family=Montserrat:wght@300;400;500;600;700;800&display=swap">
<style>
:root{
  --ink:#ffffff;
  --ink-soft:#d8d8d8;
  --bg-deep:#050608;
  --bg-panel:#131313;
  --btn:#5c5c5c;
  --field:#ffffff;
  --field-text:#555555;
}
*{box-sizing:border-box;margin:0;padding:0}
html,body{width:1200px;height:3850px;overflow:hidden}
body{background:var(--bg-deep);color:var(--ink);font-family:'Montserrat',sans-serif;position:relative}
section,footer,header{position:absolute;left:0;width:1200px}
.abs{position:absolute}
.brand{display:flex;flex-direction:column;align-items:center;gap:10px}
.brand-dot{width:56px;height:56px;border-radius:50%;border:3px solid var(--ink)}
.brand-name{font-size:27px;font-weight:400;letter-spacing:6px;color:var(--ink);font-family:'Montserrat',sans-serif}

/* hero */
.hero{top:0;height:714px;background:radial-gradient(ellipse at 60% 40%,#3a3530 0%,#1c1c1e 35%,#0b0c10 75%)}
.hero-photo{position:absolute;inset:0;background:linear-gradient(100deg,rgba(10,12,16,.9) 0%,rgba(60,55,50,.35) 55%,rgba(12,14,18,.85) 100%)}
.nav{position:absolute;top:62px;left:474px;font-size:14px;font-weight:600;letter-spacing:.3px}
.nav a{color:var(--ink);text-decoration:none;position:absolute;white-space:nowrap}
.nav a.active::after{content:"";position:absolute;left:0;right:0;bottom:-10px;height:3px;background:var(--ink)}
.hero-title{left:140px;top:300px;font-size:68px;font-weight:800;letter-spacing:.5px;line-height:1;white-space:nowrap}
.hero-title span{font-weight:300}
.hero-text{left:143px;top:414px;width:760px;font-size:19px;font-weight:500;line-height:31px}
.hero-link{left:143px;top:520px;font-size:18px;font-weight:500;color:var(--ink);text-decoration:underline;text-underline-offset:4px}

/* shared */
.heading{font-size:48px;font-weight:800;line-height:1;white-space:nowrap}
.heading span{font-weight:300}
.body-small{font-size:15px;line-height:25px;color:var(--ink-soft);font-weight:400}
.body-med{font-size:19px;line-height:30px;font-weight:400;color:var(--ink-soft)}
.btn{background:var(--btn);color:var(--ink);font-size:16px;font-weight:700;display:flex;align-items:center;justify-content:center;letter-spacing:.3px}
.photo{position:absolute}
.card-label{position:absolute;inset:0;display:flex;align-items:center;justify-content:center;font-size:33px;font-weight:700}
.play{position:absolute;left:50%;top:50%;transform:translate(-50%,-50%)}

.coaching{top:714px;height:764px;background:var(--bg-deep)}
.about{top:1478px;height:399px;background:var(--bg-panel)}
.workouts{top:1877px;height:763px;background:var(--bg-deep)}
.faq{top:2640px;height:353px;background:var(--bg-panel)}
.membership{top:2993px;height:521px;background:radial-gradient(ellipse at 50% 30%,#2c2c2c 0%,#161616 55%,#090909 100%)}
.field{background:var(--field);color:var(--field-text);font-size:12px;display:flex;align-items:center;padding-left:38px;height:54px;top:312px}

.footer{top:3514px;height:336px;background:var(--bg-deep)}
.footer .lines{font-size:16px;line-height:34px;color:var(--ink-soft)}
.footer .links{font-size:16px;line-height:29.5px;color:var(--ink-soft)}
.social{width:26px;height:26px;border-radius:50%;background:var(--ink)}
.legal{left:0;width:1200px;text-align:center;top:270px;font-size:16px;color:var(--ink-soft)}
</style>
</head>
<body>

<header class="hero">
  <div class="hero-photo" role="img" aria-label="Photo of a woman training with a punching bag in a dark gym"></div>
  <div class="abs brand" style="left:143px;top:14px;width:194px">
    <div class="brand-dot"></div>
    <div class="brand-name">BRENVALE</div>
  </div>
  <nav class="nav">
    <a class="active" href="#" style="left:0">HOME</a>
    <a href="#" style="left:88px">MEMBER</a>
    <a href="#" style="left:198px">WORKOUTS</a>
    <a href="#" style="left:329px">ABOUT</a>
    <a href="#" style="left:424px">CONTACT</a>
    <a href="#" style="left:538px">FAQ'S</a>
  </nav>
  <h1 class="abs hero-title">BRENVALE <span>COACHING</span></h1>
  <p class="abs hero-text">Lorem ipsum dolor sit amet, consectetur adipiscing elit, sed do eiusmod tempor incididunt ut labore et dolore magna aliqua.</p>
  <a class="abs hero-link" href="#">BOOK AA APPOINTMENT</a>
</header>

<section class="coaching">
  <h2 class="abs heading" style="left:143px;top:92px">OUR <span>COACHING</span></h2>
  <div class="photo" style="left:143px;top:184px;width:444px;height:288px;background:linear-gradient(135deg,#4a4d52,#2a2b2e 60%,#3b3a38)" role="img" aria-label="Photo of a coach training a woman with a kettlebell">
    <div class="card-label">BrenVale Coaching</div>
  </div>
  <div class="photo" style="left:611px;top:184px;width:444px;height:288px;background:linear-gradient(135deg,#3c3f44,#24252a 55%,#46423e)" role="img" aria-label="Photo of a coach holding a bag for a young boxer">
    <div class="card-label">BrenVale 4 Kids</div>
  </div>
  <p class="abs body-small" style="left:143px;top:518px;width:920px">Lorem ipsum dolor sit amet, consectetur adipiscing elit, sed do eiusmod tempor incididunt ut labore et dolore magna aliqis ipsum suspendisse ultricesisus commodo viverra maecenas accumsan lacus vel facilisis.</p>
  <div class="abs btn" style="left:144px;top:610px;width:192px;height:60px">SUBSCRIBE</div>
</section>

<section class="about">
  <h2 class="abs heading" style="left:142px;top:92px;line-height:60px">ABOUT<br><span>BRENVALE COACHING</span></h2>
  <p class="abs body-med" style="left:144px;top:224px;width:540px">Lorem ipsum dolor sit amet, consectetur adipiscing elit, sed do eiusmod tempor incididunt ut labore et dolore magna aliquuis ipsum</p>
  <p class="abs body-small" style="left:768px;top:134px;width:300px;font-size:14px;line-height:23px">Lorem ipsum dolor sit amet, consectetur adipiscin eiusmod tempor incididunt</p>
  <div class="abs btn" style="left:768px;top:215px;width:287px;height:58px">BOOK AN APPOINTMENT</div>
</section>

<section class="workouts">
  <h2 class="abs heading" style="left:143px;top:92px">WORKOUTS</h2>
  <div class="photo" style="left:143px;top:185px;width:444px;height:288px;background:linear-gradient(120deg,#2c2e33,#3d5a78 40%,#1f2c46 70%,#2b2b2e)" role="img" aria-label="Workout video: trainer coaching an older man at a cable machine">
    <svg class="play" width="32" height="32" viewBox="0 0 32 32"><circle cx="16" cy="16" r="15" fill="#fff"/><path d="M12 9 L24 16 L12 23 Z" fill="#111"/></svg>
  </div>
  <div class="photo" style="left:611px;top:185px;width:444px;height:288px;background:linear-gradient(120deg,#1b1c20,#2f3136 45%,#5a6a82 75%,#1c1d22)" role="img" aria-label="Workout video: trainer spotting a dumbbell press on a bench">
    <svg class="play" width="32" height="32" viewBox="0 0 32 32"><circle cx="16" cy="16" r="15" fill="#fff"/><path d="M12 9 L24 16 L12 23 Z" fill="#111"/></svg>
  </div>
  <p class="abs body-small" style="left:143px;top:519px;width:920px">Lorem ipsum dolor sit amet, consectetur adipiscing elit, sed do eiusmod tempor incididunt ut labore et dolore magna aliqis ipsum suspendisse ultricesisus commodo viverra maecenas accumsan lacus vel facilisis.</p>
  <div class="abs btn" style="left:144px;top:610px;width:192px;height:60px">VIEW MORE</div>
</section>

<section class="faq">
  <h2 class="abs heading" style="left:142px;top:85px">FAQ’S</h2>
  <p class="abs body-med" style="left:144px;top:172px;width:540px">Lorem ipsum dolor sit amet, consectetur adipiscing elit, sed do eiusmod tempor incididunt ut labore et dolore magna aliquuis ipsum</p>
  <p class="abs body-small" style="left:768px;top:85px;width:300px;font-size:14px;line-height:23px">Lorem ipsum dolor sit amet, consectetur adipiscin eiusmod tempor incididunt</p>
  <div class="abs btn" style="left:768px;top:182px;width:287px;height:59px">GO TO FAQ</div>
</section>

<section class="membership" role="img" aria-label="Dark toned photo of three athletes standing side by side">
  <h2 class="abs heading" style="left:0;width:1200px;top:148px;text-align:center">MEMBERSHIP</h2>
  <p class="abs" style="left:0;width:1200px;top:232px;text-align:center;font-size:15.5px;color:var(--ink-soft)">Sign up to receive news and updates.</p>
  <div class="abs field" style="left:150px;width:230px">First Name</div>
  <div class="abs field" style="left:392px;width:230px">Last Name</div>
  <div class="abs field" style="left:634px;width:230px">Email Address</div>
  <div class="abs btn" style="left:876px;top:312px;width:173px;height:54px;font-size:15px">SUBSCRIBE</div>
</section>

<footer class="footer">
  <div class="abs brand" style="left:143px;top:40px;width:224px">
    <div class="brand-dot" style="width:66px;height:66px"></div>
    <div class="brand-name" style="font-size:30px">BRENVALE</div>
  </div>
  <div class="abs lines" style="left:472px;top:72px">48 Cedar Lane<br>Pine Hollow, CA<br>+1 (530) 010-0199</div>
  <div class="abs links" style="left:720px;top:74px">Store<br>Booking Appointments<br>Bookshelf<br>email campaign<br>Blog</div>
  <div class="abs social" style="left:984px;top:84px" aria-label="Social link"></div>
  <div class="abs social" style="left:1026px;top:84px" aria-label="Social link"></div>
  <p class="abs legal">© 2022 BrenVale Coaching. All rights reserved &nbsp;|&nbsp; Privacy &nbsp;|&nbsp; Terms of Use</p>
</footer>

</body>
</html>
```